We need a business card design for a new company located in Lakemont, OR, entitled 'BrightPath Chiropractic & Holistic Center'. Our services include restoration of health and vitality, spinal exam, health assessment, dietary & fitness programs, lymphatic & therapeutic massage, detox & remineralize body wraps, far infrared sauna therapy

Industry/Entity Type

Business

Contact Information for Business Card

BrightPath Chiropractic & Holistic Center, Marlene Okafor LMT, 4215 Elm Ridge Rd., Suite 310, Lakemont, OR 77482, 503-555-0193

```html
<!DOCTYPE html>
<html lang="en">
<head>
<meta charset="utf-8">
<title>BrightPath Chiropractic &amp; Holistic Center – Business Card</title>
<link href="https://fonts.googleapis.com/css2?family=Libre+Baskerville:ital,wght@0,400;0,700;1,400&family=Open+Sans:wght@400;600&display=swap" rel="stylesheet">
<style>
  :root {
    --teal: #169a82;
    --navy: #1f5b8c;
    --ink: #1d1f1f;
    --ink-soft: #4a4d4d;
    --paper: #f7f7f5;
    --stage: #e4e2dd;
    --serif: "Libre Baskerville", Georgia, serif;
    --sans: "Open Sans", Arial, sans-serif;
  }
  * { box-sizing: border-box; margin: 0; padding: 0; }
  html, body { width: 1200px; height: 902px; overflow: hidden; }
  body {
    background: var(--stage);
    display: flex;
    flex-direction: column;
    align-items: center;
    justify-content: center;
    gap: 40px;
  }
  .card {
    position: relative;
    width: 700px;
    height: 400px;
    overflow: hidden;
    box-shadow: 0 6px 18px rgba(0,0,0,.18);
  }

  /* Back side: services */
  .card--back { background: var(--teal); color: var(--ink); }
  .card--back .rule {
    position: absolute; left: 40px; right: 40px; height: 1.5px; background: var(--ink);
  }
  .rule--top { top: 34px; }
  .rule--under { top: 108px; }
  .services-title {
    position: absolute; left: 44px; top: 52px;
    font-family: var(--serif); font-weight: 700; font-size: 40px; line-height: 1;
  }
  .services-list {
    position: absolute; left: 44px; top: 126px;
    list-style: none;
    font-family: var(--serif); font-size: 19px; line-height: 34px;
  }
  .services-list li { display: flex; align-items: center; gap: 14px; }
  .services-list svg { width: 16px; height: 16px; flex: none; }

  /* Front side: identity */
  .card--front { background: var(--paper); }
  .front-wave { position: absolute; inset: 0; width: 100%; height: 100%; }
  .brand {
    position: absolute; left: 30px; top: 226px;
    display: flex; align-items: center; gap: 12px;
  }
  .brand-dot { width: 40px; height: 40px; border-radius: 50%; background: var(--navy); flex: none; }
  .brand-name {
    font-family: var(--serif); font-size: 30px; color: var(--ink); line-height: 1;
  }
  .brand-tagline {
    position: absolute; left: 32px; top: 278px;
    font-family: var(--sans); font-size: 15px; color: var(--ink);
  }
  .person {
    position: absolute; right: 38px; top: 34px; text-align: right;
  }
  .person-name { font-family: var(--serif); font-weight: 400; font-size: 32px; color: var(--ink); line-height: 1.1; }
  .person-role { font-family: var(--serif); font-size: 17px; color: var(--ink-soft); margin-top: 4px; }
  .contact {
    position: absolute; right: 38px; top: 172px; text-align: right;
    list-style: none;
    font-family: var(--sans); font-size: 14px; color: var(--ink); line-height: 25px;
  }
  .contact li { display: flex; justify-content: flex-end; align-items: center; gap: 8px; }
  .contact .icon {
    width: 15px; height: 15px; background: var(--ink); flex: none;
    display: inline-flex; align-items: center; justify-content: center;
  }
  .contact .icon svg { width: 11px; height: 11px; }
  .contact .no-icon { width: 15px; flex: none; }
</style>
</head>
<body>

  <section class="card card--back" aria-label="Business card back: services">
    <div class="rule rule--top"></div>
    <h2 class="services-title">Services</h2>
    <div class="rule rule--under"></div>
    <ul class="services-list">
      <li><svg viewBox="0 0 16 16"><circle cx="8" cy="8" r="6" fill="none" stroke="#1d1f1f" stroke-width="1.4"/><circle cx="8" cy="8" r="2.2" fill="#1d1f1f"/></svg>restoration of health and vitality</li>
      <li><svg viewBox="0 0 16 16"><circle cx="8" cy="8" r="6" fill="none" stroke="#1d1f1f" stroke-width="1.4"/><circle cx="8" cy="8" r="2.2" fill="#1d1f1f"/></svg>spinal exam</li>
      <li><svg viewBox="0 0 16 16"><circle cx="8" cy="8" r="6" fill="none" stroke="#1d1f1f" stroke-width="1.4"/><circle cx="8" cy="8" r="2.2" fill="#1d1f1f"/></svg>health assessment</li>
      <li><svg viewBox="0 0 16 16"><circle cx="8" cy="8" r="6" fill="none" stroke="#1d1f1f" stroke-width="1.4"/><circle cx="8" cy="8" r="2.2" fill="#1d1f1f"/></svg>dietary &amp; fitness programs</li>
      <li><svg viewBox="0 0 16 16"><circle cx="8" cy="8" r="6" fill="none" stroke="#1d1f1f" stroke-width="1.4"/><circle cx="8" cy="8" r="2.2" fill="#1d1f1f"/></svg>lymphatic &amp; therapeutic massage</li>
      <li><svg viewBox="0 0 16 16"><circle cx="8" cy="8" r="6" fill="none" stroke="#1d1f1f" stroke-width="1.4"/><circle cx="8" cy="8" r="2.2" fill="#1d1f1f"/></svg>detox &amp; remineralize body wraps</li>
      <li><svg viewBox="0 0 16 16"><circle cx="8" cy="8" r="6" fill="none" stroke="#1d1f1f" stroke-width="1.4"/><circle cx="8" cy="8" r="2.2" fill="#1d1f1f"/></svg>far infrared sauna therapy</li>
    </ul>
  </section>

  <section class="card card--front" aria-label="Business card front">
    <svg class="front-wave" viewBox="0 0 700 400" preserveAspectRatio="none" aria-hidden="true">
      <path d="M0 0 H360 C330 130 310 270 300 400 H0 Z" fill="var(--teal)"/>
      <path d="M360 0 C330 130 310 270 300 400" fill="none" stroke="#1d1f1f" stroke-width="3"/>
    </svg>

    <div class="brand">
      <span class="brand-dot"></span>
      <span class="brand-name">BrightPath</span>
    </div>
    <p class="brand-tagline">Chiropractic &amp; Holistic Center</p>

    <div class="person">
      <h1 class="person-name">Dana Whitfield</h1>
      <p class="person-role">Chief Executive</p>
    </div>

    <ul class="contact">
      <li>503-555-0193<span class="icon"><svg viewBox="0 0 12 12"><path d="M3 1.5 L4.6 3.8 L3.7 4.8 C4.4 6.3 5.7 7.6 7.2 8.3 L8.2 7.4 L10.5 9 L9.4 10.5 C5.5 10.2 1.8 6.5 1.5 2.6 Z" fill="#fff"/></svg></span></li>
      <li>dana.whitfield@brightpathholistic.com<span class="icon"><svg viewBox="0 0 12 12"><rect x="1.5" y="3" width="9" height="6" fill="none" stroke="#fff" stroke-width="1"/><path d="M1.5 3 L6 6.5 L10.5 3" fill="none" stroke="#fff" stroke-width="1"/></svg></span></li>
      <li>www.brightpathholistic.com<span class="icon"><svg viewBox="0 0 12 12"><circle cx="6" cy="6" r="4.3" fill="none" stroke="#fff" stroke-width="1"/><path d="M1.7 6 H10.3 M6 1.7 C3.8 4 3.8 8 6 10.3 M6 1.7 C8.2 4 8.2 8 6 10.3" fill="none" stroke="#fff" stroke-width=".8"/></svg></span></li>
      <li>Marlene Okafor LMT, 4215 Elm Ridge Rd.,<span class="icon"><svg viewBox="0 0 12 12"><path d="M6 11 C3.5 7.8 2.5 6.2 2.5 4.6 A3.5 3.5 0 0 1 9.5 4.6 C9.5 6.2 8.5 7.8 6 11 Z" fill="#fff"/><circle cx="6" cy="4.6" r="1.3" fill="#1d1f1f"/></svg></span></li>
      <li>Suite 310, Lakemont, OR 97482<span class="no-icon"></span></li>
    </ul>
  </section>

</body>
</html>
```